Modern card design needed for building development company

We are looking for a sharp modern new look for our business cards.
We are a New Zealand based company called TKR Ventures NZ LTD that specialises in subdividing large sections, housing and commercial buildings.
We have attached a photo of the current logo and would like to see it improved somehow as it looks a bit dated.
We are open to any colours.

Target Market(s)

Investors, Property buyers

Industry/Entity Type

Investment

Contact Information for Business Card

TKR VENTURES NZ LTD
www.tkrventuresnz.co.nz

Damon Whitcombe
Phone +64 21 938 104
Email dpwhitcombe@korumail.co.nz

Font styles to use
Serif
Sans Serif

Colors
0792cd
33a6d7
85cae6
6b449b
886aae
f04a50
ec1f27
f37122
f68d4d

Requirements
Must have
• Please try and make the logo more modern or if you have a similar one we would like to see it.

```html
<!DOCTYPE html>
<html lang="en">
<head>
<meta charset="utf-8">
<title>TKR Ventures NZ LTD – Business Card</title>
<link href="https://fonts.googleapis.com/css2?family=Montserrat:wght@600;700&family=Work+Sans:wght@300;400&display=swap" rel="stylesheet">
<style>
  :root {
    --backdrop: #e8e5e1;
    --card-white: #ffffff;
    --charcoal: #232323;
    --brand-red: #8b1a2b;
    --ink: #2a2a2a;
    --light-text: #f2f2f2;
  }
  * { box-sizing: border-box; margin: 0; padding: 0; }
  html, body { width: 1200px; height: 930px; overflow: hidden; }
  body {
    position: relative;
    background: var(--backdrop);
    font-family: "Work Sans", Arial, sans-serif;
  }
  .card {
    position: absolute;
    left: 278px;
    width: 644px;
    height: 370px;
    box-shadow: 0 6px 18px rgba(0,0,0,0.18);
    overflow: hidden;
  }
  .card--front { top: 75px; background: var(--card-white); }
  .card--back { top: 486px; background: var(--charcoal); }

  .company-mark {
    position: absolute;
    right: 32px;
    top: 34px;
    width: 176px;
    display: flex;
    flex-direction: column;
    align-items: center;
    gap: 14px;
    font-family: "Montserrat", Arial, sans-serif;
    font-weight: 600;
    font-size: 12px;
    letter-spacing: 1.5px;
    color: var(--ink);
    white-space: nowrap;
  }
  .company-mark__square {
    width: 126px; height: 126px;
    background: var(--brand-red);
  }

  .person { position: absolute; left: 32px; top: 190px; }
  .person__name {
    font-family: "Montserrat", Arial, sans-serif;
    font-weight: 700;
    font-size: 21px;
    letter-spacing: 0.4px;
    color: var(--brand-red);
    line-height: 1.15;
  }
  .person__title {
    font-weight: 300;
    font-size: 16px;
    color: var(--ink);
    margin-top: 1px;
  }

  .info-band {
    position: absolute;
    left: 0; top: 248px;
    width: 100%; height: 99px;
    background: var(--charcoal);
    color: var(--light-text);
    font-weight: 300;
    font-size: 15.5px;
    line-height: 20px;
  }
  .info-band__chevron { position: absolute; left: 0; top: 0; }
  .contact-list {
    position: absolute; left: 32px; top: 22px;
    list-style: none;
  }
  .contact-list li { display: flex; align-items: center; gap: 10px; }
  .contact-list svg { width: 12px; height: 12px; flex: none; }
  .postal-address {
    position: absolute; right: 32px; top: 22px;
    text-align: right; font-style: normal;
  }

  .back-mark {
    position: absolute;
    left: 0; right: 0; top: 92px;
    display: flex; flex-direction: column; align-items: center;
    gap: 20px;
    font-family: "Montserrat", Arial, sans-serif;
    font-weight: 600;
    font-size: 16px;
    letter-spacing: 2.6px;
    color: #ffffff;
    white-space: nowrap;
  }
  .back-mark__square { width: 160px; height: 160px; background: #ffffff; }
</style>
</head>
<body>

<section class="card card--front">
  <div class="company-mark">
    <span class="company-mark__square"></span>
    <span>TKR VENTURES NZ LTD</span>
  </div>

  <div class="person">
    <h1 class="person__name">DAMON WHITCOMBE</h1>
    <p class="person__title">Director</p>
  </div>

  <div class="info-band">
    <svg class="info-band__chevron" width="30" height="99" viewBox="0 0 30 99">
      <polygon points="0,1 27,30 27,69 0,98" fill="var(--brand-red)" stroke="#ffffff" stroke-width="1.5"/>
    </svg>
    <ul class="contact-list">
      <li>
        <svg viewBox="0 0 12 12"><path d="M3 1 L5 3.5 L4 5 Q5.5 7.5 7 8 L8.5 7 L11 9 L9.5 11 Q4 10 1 3 Z" fill="#ffffff"/></svg>
        <span>+64 21 938 104</span>
      </li>
      <li>
        <svg viewBox="0 0 12 12"><rect x="1" y="2.5" width="10" height="7" fill="none" stroke="#ffffff" stroke-width="1.2"/><path d="M1 3 L6 7 L11 3" fill="none" stroke="#ffffff" stroke-width="1.2"/></svg>
        <span>dpwhitcombe@korumail.co.nz</span>
      </li>
      <li>
        <svg viewBox="0 0 12 12"><circle cx="6" cy="6" r="5" fill="none" stroke="#ffffff" stroke-width="1"/><ellipse cx="6" cy="6" rx="2.2" ry="5" fill="none" stroke="#ffffff" stroke-width="0.9"/><path d="M1 6 H11 M2 3.5 H10 M2 8.5 H10" stroke="#ffffff" stroke-width="0.8"/></svg>
        <span>www.tkrventuresnz.co.nz</span>
      </li>
    </ul>
    <address class="postal-address">
      PO BOX 48215<br>
      Northcote Auckland<br>
      New Zealand
    </address>
  </div>
</section>

<section class="card card--back">
  <div class="back-mark">
    <span class="back-mark__square"></span>
    <span>TKR VENTURES NZ LTD</span>
  </div>
</section>

</body>
</html>
```